Web Design Project - Shipping Industry

Goals and Objectives
The objective of the new website is to create a more modern look and feel. The site will also allow for a more effective means of communicating with members while providing the public with information and developments in the local, regional and international shipping industry.
Scope
The website will highlight the history of the organisation inclusive of text and photographs. It will take visitors through the years from beginning to present. Information on the history of the shipping industry will also be included.
It will feature current articles on the organisation, its members and stakeholders in the shipping industry. Member information as well as pertinent details regarding the organisation’s subsidiaries will be documented for the website.
Information as it relates to shipping statistics, case studies, laws and regulations, international treaties and trade documents, shipping terms, careers in shipping, job opportunities, training opportunities, information for shippers including port listing and trade lanes will be main features of the content for the website.
The Association’s community involvement, industry calendar events and related links relevant industry members will also be featured.
Target Market
• The General Public;
• Members of the organization;
• Shipping Industry Stakeholders (local, regional and international);
• Tertiary students conducting research.
• Potential employees
• Potential Business Partners
Best Practice Bench Marketing
The following websites are being looked at:
• Korvel Quayworks - http://www.korvelquayworks.example/ (preferred look)
• Tessaly Maritime Association - http://www.tma-freight.example/ (like image transition on main page)
• Drovna - http://www.drovna.example (professional look)
• PLW - http://www.pelworth.example (preferred color: blue in logo)
• Quillo - http://www.quillo.example/electronics/tv-video-audio/ (preferred look for links page: image + short text below + visit site link)
Expected Result
• 3 - 5 pages which must include: [1] main page [2] standard page [3] links page

```html
<!DOCTYPE html>
<html lang="en">
<head>
<meta charset="utf-8">
<title>Meridane – Global Shipper</title>
<link href="https://fonts.googleapis.com/css2?family=Arimo:wght@400;700&family=Teko:wght@500;600&family=PT+Sans:wght@400&display=swap" rel="stylesheet">
<style>
  :root{
    --navy-deep:#0b1c63;
    --navy:#142f9a;
    --royal:#2d4fc4;
    --sky:#3a5ccf;
    --ink:#1b2f96;
    --text:#555b66;
    --muted:#8a8f99;
    --white:#ffffff;
    --band:#eef0f5;
    --gold:#f2b316;
    --orange:#d6901a;
    --panel-top:#dfe4ee;
  }
  *{box-sizing:border-box;margin:0;padding:0}
  html,body{width:885px;height:1200px;overflow:hidden}
  body{
    position:relative;
    font-family:"Arimo",Arial,sans-serif;
    background:linear-gradient(180deg,var(--navy-deep) 0%,#1b3aa6 55%,var(--sky) 100%);
  }
  .page{position:absolute;left:17px;top:0;width:850px;height:1136px;background:var(--white)}
  .abs{position:absolute}

  /* header */
  .brand{left:10px;top:40px;font-family:"Teko",sans-serif;font-weight:500;font-size:40px;letter-spacing:6px;color:var(--navy);line-height:40px}
  .brand-dot{display:inline-block;width:10px;height:10px;background:var(--navy);margin-left:6px;vertical-align:6px}
  .locator-map{left:538px;top:33px;width:54px;height:42px;border-radius:6px;background:radial-gradient(circle,#2d6fe0 0%,#1d4fbf 70%,transparent 72%)}
  .locate{left:617px;top:49px;font-size:12px;color:var(--orange)}
  .search{left:687px;top:43px;width:158px;height:24px;border:1px solid #c6c8cc;border-radius:6px;background:linear-gradient(#f4f4f4,#fff)}
  .search svg{position:absolute;right:6px;top:4px}

  /* nav */
  .nav{left:0;top:104px;width:850px;height:46px;background:linear-gradient(180deg,#1f3dac 0%,#102a8c 60%,#0e2478 100%);display:flex}
  .nav a{display:block;padding:0 14px;line-height:46px;font-size:12px;font-weight:700;color:var(--white);text-decoration:none;border-right:1px solid #0a1b5e;box-shadow:1px 0 0 #2b49b6}
  .nav a.active{color:var(--gold)}
  .nav-rule{left:0;top:150px;width:850px;height:7px;background:#d9dbe0}

  /* hero */
  .hero{left:0;top:157px;width:850px;height:370px;background:linear-gradient(180deg,#bfcbd6 0%,#dde4ea 35%,#7aa0b8 62%,#4d6f86 100%)}
  .hero-caption{left:0;top:273px;width:850px;height:97px;background:rgba(16,36,110,.88)}
  .hero-title{left:25px;top:12px;font-family:"Teko",sans-serif;font-weight:500;font-size:31px;color:var(--white);letter-spacing:1px;line-height:32px}
  .hero-text{left:25px;top:46px;width:760px;font-size:11px;line-height:19px;color:var(--white)}
  .hero-next{left:790px;top:16px}

  /* columns */
  .col-head{height:42px;background:var(--band);border-bottom:2px solid var(--navy);font-family:"Teko",sans-serif;font-weight:600;font-size:31px;color:var(--ink);padding-left:11px;line-height:48px;letter-spacing:.5px}
  .col-photo{height:136px;margin-top:12px}
  .col-text{margin-top:13px;padding-left:4px;font-size:11px;line-height:19px;color:var(--text);width:262px}
  .btn{display:block;width:98px;height:30px;margin:20px 0 0 4px;background:linear-gradient(#2340b4,#0d2275);color:var(--gold);font-size:12px;text-align:center;line-height:30px;text-decoration:none;box-shadow:0 2px 0 #c5c8cf}
  .adv-list{list-style:none;margin-top:12px}
  .adv-list li{position:relative;padding-left:40px;height:27px;font-size:11px;color:var(--text);line-height:20px}
  .adv-list li::before{content:"";position:absolute;left:15px;top:6px;border-left:5px solid #9a9ea6;border-top:4px solid transparent;border-bottom:4px solid transparent}

  /* partners & login */
  .footer-rule{left:0;top:958px;width:855px;height:4px;background:var(--navy)}
  .partner{width:112px;height:40px;background:#d2d4d8;border-radius:3px}
  .login{left:582px;top:967px;width:259px;height:169px;background:linear-gradient(180deg,var(--panel-top) 0%,#f4f6fa 100%)}
  .login h2{position:absolute;left:0;top:8px;width:100%;text-align:center;font-family:"PT Sans",sans-serif;font-weight:400;font-size:16px;color:#283a6e}
  .login label{position:absolute;left:23px;font-family:"PT Sans",sans-serif;font-style:italic;font-size:12px;color:#8a8f99}
  .login .field{position:absolute;left:83px;width:163px;height:29px;background:var(--white);border:1px solid #c7cad1}
  .login .submit{position:absolute;left:85px;top:126px;width:98px;height:29px;background:linear-gradient(#2340b4,#0d2275);color:var(--white);font-size:11px;text-align:center;line-height:29px}

  /* bottom bar */
  .bottom-links{left:26px;top:1153px;font-size:11px;color:var(--white)}
  .bottom-links span{margin:0 10px;opacity:.8}
  .copyright{left:499px;top:1154px;font-size:10px;font-weight:700;color:var(--white)}
  .social{top:1147px;width:25px;height:25px;border-radius:50%;background:linear-gradient(#c9ccd2,#8b8f97)}
</style>
</head>
<body>
<div class="page">
  <header>
    <div class="abs brand">MERIDANE<span class="brand-dot"></span></div>
    <div class="abs locator-map" role="img" aria-label="Small world map icon"></div>
    <div class="abs locate">Locate Us</div>
    <div class="abs search">
      <svg width="14" height="14" viewBox="0 0 14 14"><circle cx="6" cy="6" r="4.5" fill="none" stroke="#aaa" stroke-width="1.5"/><line x1="9.3" y1="9.3" x2="13" y2="13" stroke="#aaa" stroke-width="1.8"/></svg>
    </div>
  </header>

  <nav class="abs nav">
    <a class="active">Home</a><a>About Us</a><a>Sustainability</a><a>News</a><a>Careers</a><a>Links</a><a>Contact Us</a>
  </nav>
  <div class="abs nav-rule"></div>

  <section class="abs hero" role="img" aria-label="Large container ship sailing at sea under a cloudy sky">
    <div class="abs hero-caption">
      <div class="abs hero-title">GLOBAL SHIPPER</div>
      <p class="abs hero-text">Lorem ipsum dolor sit amet, consectetuer adipiscing elit, sed diam nonummy nibh euismod tincidunt ut laoreet dolore magna aliquam erat volutpat. Ut wisi enim ad minim veniam, quis nostrud exerci tation ullamcorper suscipit lobortis nisl ut aliquip ex ea commodo consequat.</p>
      <svg class="abs hero-next" width="40" height="64" viewBox="0 0 40 64"><polygon points="2,2 18,2 38,32 18,62 2,62 22,32" fill="#b9c2d8"/></svg>
    </div>
  </section>

  <section class="abs" style="left:15px;top:554px;width:262px">
    <h2 class="col-head">ABOUT US</h2>
    <div class="col-photo" role="img" aria-label="Loaded container ship at sea" style="background:linear-gradient(180deg,#8a98ad 0%,#c4ccd6 45%,#3c5fa8 70%,#254a86 100%)"></div>
    <p class="col-text">Lorem ipsum dolor sit amet, consectetuer adipiscing elit, sed diam nonummy nibh euismod tincidunt ut laoreet dolore magna aliquam erat volutpat. Ut wisi enim ad minim veniam, quis nostrud exerci tation ullamcorper suscipit lobortis nisl ut aliquip ex ea commodo consequat.</p>
    <a class="btn">Read More</a>
  </section>

  <section class="abs" style="left:294px;top:554px;width:262px">
    <h2 class="col-head" style="padding-left:21px">OUR SERVICES</h2>
    <div class="col-photo" role="img" aria-label="Port cranes lit at dusk" style="background:linear-gradient(180deg,#3b4a7a 0%,#a05a5a 40%,#c77a3c 62%,#1c2236 100%)"></div>
    <p class="col-text">Lorem ipsum dolor sit amet, consectetuer adipiscing elit, sed diam nonummy nibh euismod tincidunt ut laoreet dolore magna aliquam erat volutpat. Ut wisi enim ad minim veniam, quis nostrud exerci tation ullamcorper suscipit lobortis nisl ut aliquip ex ea commodo consequat.</p>
    <a class="btn">Read More</a>
  </section>

  <section class="abs" style="left:568px;top:554px;width:263px">
    <h2 class="col-head" style="padding-left:19px">OUR ADVANTAGES</h2>
    <ul class="adv-list">
      <li>Praesent volutpat orci vitae lorem</li>
      <li>Morbi sed justo at nisl pulvinar</li>
      <li>Maecenas varius tortor eu magna hendrer</li>
      <li>Proin nec erat at nibh posuere</li>
      <li>Praesent fringilla enim eget massa sagitti</li>
      <li>Praesent volutpat orci vitae lorem</li>
      <li>Morbi sed justo at nisl pulvinar</li>
      <li>Maecenas varius tortor eu magna hendrer</li>
      <li>Proin nec erat at nibh posuere</li>
      <li>Praesent fringilla enim eget massa sagitti</li>
    </ul>
  </section>

  <div class="abs footer-rule"></div>

  <div class="abs partner" style="left:78px;top:992px"></div>
  <div class="abs partner" style="left:226px;top:992px"></div>
  <div class="abs partner" style="left:374px;top:992px"></div>
  <div class="abs partner" style="left:78px;top:1069px"></div>
  <div class="abs partner" style="left:226px;top:1069px"></div>
  <div class="abs partner" style="left:374px;top:1069px"></div>

  <form class="abs login">
    <h2>Members Login</h2>
    <label style="top:46px">Username</label><div class="field" style="top:39px"></div>
    <label style="top:92px">Password</label><div class="field" style="top:85px"></div>
    <div class="submit">SUBMIT</div>
  </form>
</div>

<div class="abs bottom-links">Home<span>|</span>About us<span>|</span>Services<span>|</span>Location<span>|</span>Contact</div>
<div class="abs copyright">Copyrights Reserved 2012 @ Meridane PCS</div>
<div class="abs social" style="left:717px"></div>
<div class="abs social" style="left:757px"></div>
<div class="abs social" style="left:797px"></div>
<div class="abs social" style="left:834px"></div>
</body>
</html>
```